Heron Loan Partners Business Card

We need a business card design for our mortgage servicing company. In addition to servicing the loans of homeowners, we help homeowners with purchasing their homes and any mortgage refinancing. We would like to see designs that use the colors in the logo attached below (gold-ish yellow and navy blue), and any other design you deem fit! The design should communicate a simpler life with smart mortgages provided by Heron.

```html
<!DOCTYPE html>
<html lang="en">
<head>
<meta charset="utf-8">
<title>Heron Loan Partners Business Card</title>
<link rel="stylesheet" href="https://fonts.googleapis.com/css2?family=Arimo:wght@400;700&display=swap">
<style>
  :root {
    --navy: #221d55;
    --gold: #e3b23c;
    --white: #ffffff;
    --stage: #3a3a3c;
    --divider: #8f8bb5;
  }
  * { box-sizing: border-box; margin: 0; padding: 0; }
  html, body { width: 1200px; height: 689px; overflow: hidden; }
  body {
    background: var(--stage);
    font-family: "Arimo", Arial, sans-serif;
    position: relative;
  }
  .card {
    position: absolute;
    top: 190px;
    width: 530px;
    height: 310px;
    border-radius: 16px;
    overflow: hidden;
  }
  .card-front { left: 45px; background: var(--navy); }
  .card-back { left: 625px; background: var(--white); }

  .brand-name {
    color: var(--gold);
    font-weight: 700;
    letter-spacing: 0.5px;
    white-space: nowrap;
  }
  .card-front .brand {
    position: absolute;
    top: 105px; left: 0; right: 0;
    text-align: center;
  }
  .card-front .brand-name { font-size: 40px; }
  .tagline {
    position: absolute;
    top: 205px; left: 0; right: 0;
    text-align: center;
    color: var(--white);
    font-size: 15px;
  }

  .card-back .brand {
    position: absolute;
    top: 0; left: 0; right: 0; height: 150px;
    display: flex; align-items: center; justify-content: center;
  }
  .card-back .brand-name { font-size: 32px; color: var(--navy); }
  .gold-rule {
    position: absolute;
    top: 150px; left: 0; right: 0; height: 4px;
    background: var(--gold);
  }
  .info-band {
    position: absolute;
    top: 154px; left: 0; right: 0; bottom: 0;
    background: var(--navy);
    display: flex; align-items: center; justify-content: center;
    gap: 18px;
  }
  .person { text-align: right; color: var(--white); font-size: 13px; line-height: 1.35; }
  .person-name { color: var(--gold); font-weight: 700; font-size: 22px; line-height: 1.2; }
  .divider { width: 1px; height: 92px; background: var(--divider); }
  .contacts { list-style: none; color: var(--white); font-size: 13px; line-height: 1.55; }
  .contacts li { display: flex; align-items: center; gap: 8px; }
  .contacts svg { width: 11px; height: 11px; fill: var(--gold); flex: none; }
</style>
</head>
<body>
  <section class="card card-front">
    <div class="brand"><span class="brand-name">Heron Loan Partners</span></div>
    <p class="tagline">Simpler life with smart mortgages</p>
  </section>

  <section class="card card-back">
    <div class="brand"><span class="brand-name">Heron Loan Partners</span></div>
    <div class="gold-rule"></div>
    <div class="info-band">
      <div class="person">
        <p class="person-name">Daniel Reyes</p>
        <p class="person-title">President</p>
        <p>412 Willow Bend Road</p>
        <p>Halden, Canada 20418</p>
      </div>
      <div class="divider"></div>
      <ul class="contacts">
        <li><svg viewBox="0 0 12 12" aria-hidden="true"><path d="M2.5 0.8l2 2.2-1 1.3c.7 1.6 1.7 2.6 3.3 3.3l1.3-1 2.2 2-1.2 2.4C5 10.8 1.2 7 0.9 2z"/></svg>555-210-4830</li>
        <li><svg viewBox="0 0 12 12" aria-hidden="true"><path d="M3 0h6v12H3zM4 1.5v8h4v-8z"/></svg>555-318-2276</li>
        <li><svg viewBox="0 0 12 12" aria-hidden="true"><path d="M0 2h12v8H0zM1 3l5 3.5L11 3v-.2H1z"/></svg>info@heronloanpartners.com</li>
        <li><svg viewBox="0 0 12 12" aria-hidden="true"><circle cx="6" cy="6" r="5.5"/><path d="M0.5 6h11M6 0.5c2 2 2 9 0 11M6 0.5c-2 2-2 9 0 11" stroke="#221d55" stroke-width="0.8" fill="none"/></svg>www.heronloanpartners.com</li>
      </ul>
    </div>
  </section>
</body>
</html>
```